Health Clinic treating people with mental illness needs a website

We need a website for a new mental health clinic based in Florida called Solvane Wellness USA. We treat people with mental health issues such as depression, PTSD, Bipolar, chronic pain, etc. I want the website to be easy to follow and inviting to the visitors. It should be easy to locate the different treatment options and how to go about contacting and making appointments. The images on the website should be something that the patients can relate to, whether a close up of a woman's face, something that conveys emotion. The patients visiting this website are often sad and miserable, they need to be able to feel comfortable when they look at this website. I want them to feel that we understand where they are coming from. I like colors such as purple, turquoise, lavender.

Target Market(s)

College students, veterans, anyone with mental illness

Industry/Entity Type

Health And Wellness

Font styles to use
Serif
Sans Serif

Colors

Designer to choose colors to be used in the design.

Requirements
Must have
• There should be a home/landing page, about us page, treatment page, contact page, and a FAQ page. I've included my logo below.
Nice to have
• The flow of the web pages should be calming and welcoming. I want people to feel warm and understood when they enter our page.
Should not have
• The images and writing should not be overly stimulating or aggressive.

```html
<!DOCTYPE html>
<html lang="en">
<head>
<meta charset="utf-8">
<title>Solvane Wellness USA — FAQ</title>
<link href="https://fonts.googleapis.com/css2?family=IBM+Plex+Sans:wght@400;500;600;700&display=swap" rel="stylesheet">
<style>
:root{
  --ink:#222;
  --purple:#4b1a6e;
  --plum:#a0519b;
  --teal:#2eac93;
  --teal-dark:#23947d;
  --teal-light:#77c6b8;
  --line:#cfcfcf;
  --white:#fff;
  --fb:#3b5bbd;
  --tw:#1da1f2;
  --li:#15194f;
}
*{margin:0;padding:0;box-sizing:border-box}
html,body{width:1200px;height:1003px;overflow:hidden;background:var(--white)}
body{font-family:"IBM Plex Sans",sans-serif;color:var(--ink);position:relative}
.abs{position:absolute}
.brand{left:130px;top:26px;color:var(--purple);font-weight:700;line-height:1}
.brand .name{font-size:30px;display:block}
.brand .sub{font-size:12px;letter-spacing:2px;display:block;margin-top:4px;padding-left:58px}
.nav{top:45px;left:476px;display:flex;font-weight:600;font-size:15.5px;letter-spacing:.3px}
.nav a{color:var(--ink);text-decoration:none;margin-right:36px}
.nav a.current{color:var(--purple);text-decoration:underline;text-underline-offset:4px}
.social{display:flex;gap:7px}
.social span{width:27px;height:27px;border-radius:50%;display:block}
.social .fb{background:var(--fb)} .social .tw{background:var(--tw)} .social .li{background:var(--li)}
.header-social{left:973px;top:40px}
.page-title{top:170px;left:0;width:1200px;text-align:center;font-size:25px;font-weight:700;letter-spacing:.6px}
.faq-item{left:297px;width:602px;height:45px;border:1px solid var(--line);display:flex;align-items:center;padding-left:24px;font-size:16px}
.toggle{position:absolute;right:5px;top:7px;width:35px;height:30px;background:var(--teal);border:1px solid #c9e8e1}
.toggle.open{background:var(--plum)}
.toggle::before,.toggle::after{content:"";position:absolute;background:var(--white);left:50%;top:50%;transform:translate(-50%,-50%)}
.toggle::before{width:11px;height:2px}
.toggle::after{width:2px;height:11px}
.toggle.open::after{display:none}
.toggle.open::before{width:13px}
.answer{left:298px;top:308px;width:565px;font-size:13.5px;line-height:17.6px}
.footer{left:0;top:614px;width:1200px;height:332px;background:var(--teal);color:var(--white)}
.footer-brand{left:170px;top:738px;color:var(--purple);font-weight:700;line-height:1;text-align:right;width:330px}
.footer-brand .name{font-size:62px;display:block}
.footer-brand .sub{font-size:22px;letter-spacing:4px;display:block;margin-top:4px}
.follow{left:308px;top:855px;display:flex;align-items:center;gap:16px;color:var(--white);font-size:15px}
.divider{left:578px;top:663px;width:2px;height:231px;background:var(--teal-dark)}
.heading{font-weight:700;font-size:15px;color:var(--white)}
.menu-links{left:656px;top:691px;font-size:15px;color:var(--white);word-spacing:2px}
.contact{display:flex;gap:12px;color:var(--white);font-size:15px;line-height:19px}
.contact .icon{width:28px;height:28px;border-radius:50%;background:var(--white);display:flex;align-items:center;justify-content:center;margin-top:3px;flex:none}
.bottom-bar{left:0;top:946px;width:1200px;height:57px;background:var(--teal-light);text-align:center;padding-top:21px;font-size:13px;color:var(--ink)}
</style>
</head>
<body>
<header>
  <div class="abs brand"><span class="name">Solvane</span><span class="sub">WELLNESS USA</span></div>
  <nav class="abs nav">
    <a href="#">HOME</a><a href="#">ABOUT US</a><a href="#">TREATMENT</a><a href="#" class="current">FAQ</a><a href="#">CONTACT US</a>
  </nav>
  <div class="abs social header-social"><span class="fb"></span><span class="tw"></span><span class="li"></span></div>
</header>

<main>
  <h1 class="abs page-title">FREQUENTLY ASKED QUESTIONS</h1>
  <div class="abs faq-item" style="top:247px">Lorem ipsum dolor sit amet consectetur adipiscing elit?<span class="toggle open"></span></div>
  <p class="abs answer">Sed ut perspiciatis unde omnis iste natus error sit voluptatem accusantdoloremque laudantium, totam rem aper eaque ipsa quae ab illo inventore veritatis easi architecto beatae vitae dicta sunt explicabo ipsam voluptatem.</p>
  <div class="abs faq-item" style="top:386px">Lorem ipsum dolor sit amet consectetur adipiscing elit?<span class="toggle"></span></div>
  <div class="abs faq-item" style="top:444px">Lorem ipsum dolor sit amet consectetur adipiscing elit?<span class="toggle"></span></div>
  <div class="abs faq-item" style="top:501px">Lorem ipsum dolor sit amet consectetur adipiscing elit?<span class="toggle"></span></div>
</main>

<footer>
  <div class="abs footer"></div>
  <div class="abs footer-brand"><span class="name">Solvane</span><span class="sub">WELLNESS USA</span></div>
  <div class="abs follow">FOLLOW US<div class="social"><span class="fb"></span><span class="tw"></span><span class="li"></span></div></div>
  <div class="abs divider"></div>

  <div class="abs heading" style="left:654px;top:667px">MENU</div>
  <div class="abs menu-links">Home |&nbsp; About us &nbsp;|&nbsp; Treatment &nbsp;|&nbsp; FAQ &nbsp;|&nbsp;Contact us</div>
  <div class="abs heading" style="left:654px;top:751px">CONTACT US</div>

  <div class="abs contact" style="left:660px;top:792px">
    <span class="icon"><svg width="12" height="14" viewBox="0 0 12 14"><path d="M6 0a5 5 0 0 0-5 5c0 3.6 5 9 5 9s5-5.4 5-9a5 5 0 0 0-5-5z" fill="#2eac93"/><circle cx="6" cy="5" r="1.8" fill="#fff"/></svg></span>
    <div>4120 Harbor Crest Lane<br>Sarasota, FL 34231</div>
  </div>
  <div class="abs contact" style="left:898px;top:792px">
    <span class="icon"><svg width="12" height="12" viewBox="0 0 12 12"><path d="M2.4 0.8 4.2 2.9 3.3 4.3c.8 1.7 2.2 3.1 3.9 3.9l1.4-.9 2.1 1.8-.9 1.9C5.2 11 1 6.8.5 2z" fill="#2eac93"/></svg></span>
    <div>Call Us<br>555.014.2260</div>
  </div>
  <div class="abs contact" style="left:660px;top:856px">
    <span class="icon"><svg width="13" height="10" viewBox="0 0 13 10"><rect width="13" height="10" rx="1" fill="#2eac93"/><path d="M0.5 1 6.5 5.5 12.5 1" fill="none" stroke="#fff" stroke-width="1.2"/></svg></span>
    <div>E mail us<br>hello@solvanewellness.com</div>
  </div>

  <div class="abs bottom-bar">Copyright © 2019 All Rights Reserved</div>
</footer>
</body>
</html>
```